Modern Attractive Letterhead for Veterinary House Call Business.

A letterhead which can be printed on A4, A5 and A6 paper sizes.
To have: ( our files to be uploaded)
1. Logo with Text
2. telephone
3. email
4. website
5. Address

Target Market(s)

60-85year mainly women pet owners. Also market include families, young professionals, busy people who have dogs and cats

Industry/Entity Type

Business

Requirements
Must have
• 1. Logo with Text ( provided)
• 2. telephone
• 3. email
• 4. website
• 5. Address
Nice to have
• Needs to be modern, preferably warm and caring in nature( if possible )
Should not have
• difficulty in printing A5 and A6

```html
<!DOCTYPE html>
<html lang="en">
<head>
<meta charset="utf-8">
<title>Kindpaw Vet Visits – Letterhead</title>
<link href="https://fonts.googleapis.com/css2?family=Cinzel:wght@400;600&display=swap" rel="stylesheet">
<style>
  :root {
    --backdrop: #e9ecef;
    --paper: #ffffff;
    --brand-blue: #1a4fa8;
    --brand-blue-deep: #0f3f9a;
    --brand-cyan: #00b6f0;
    --brand-green: #4fb81c;
    --text-dark: #1f2430;
    --rule-grey: #b9bec6;
    --icon-blue: #1a6fd0;
  }
  * { margin: 0; padding: 0; box-sizing: border-box; }
  html, body {
    width: 982px; height: 1200px; overflow: hidden;
    background: var(--backdrop);
  }
  .letterhead {
    position: absolute; left: 43px; top: 20px;
    width: 896px; height: 1160px;
    background: var(--paper);
    box-shadow: 0 2px 10px rgba(0,0,0,.12);
    font-family: "Cinzel", "Times New Roman", serif;
    overflow: hidden;
  }
  .letterhead__shapes { position: absolute; inset: 0; width: 100%; height: 100%; }

  .brand {
    position: absolute; left: 118px; top: 72px;
    display: flex; align-items: center; gap: 12px;
  }
  .brand__dot {
    width: 22px; height: 22px; border-radius: 50%;
    background: var(--brand-green);
  }
  .brand__name {
    font-size: 34px; font-weight: 600; letter-spacing: 1px;
    color: var(--brand-blue); line-height: 1;
  }

  .contact {
    position: absolute; left: 582px; top: 40px;
    list-style: none;
    font-size: 17px; color: var(--text-dark);
  }
  .contact__item {
    display: flex; align-items: center; gap: 8px;
    height: 29px;
  }
  .contact__icon { width: 17px; height: 17px; flex: none; }

  .address {
    position: absolute; right: 33px; top: 1092px;
    text-align: right; color: #fff;
    font-size: 17px; line-height: 24px; font-style: normal;
  }
  .address__line { display: flex; justify-content: flex-end; align-items: center; gap: 8px; }
  .address__icon { width: 17px; height: 17px; }
</style>
</head>
<body>
<main class="letterhead">
  <svg class="letterhead__shapes" viewBox="0 0 815 1055" preserveAspectRatio="none" aria-hidden="true">
    <defs>
      <linearGradient id="band-blue" x1="0" y1="0" x2="0" y2="1">
        <stop offset="0" stop-color="#1d5cc4"/>
        <stop offset="1" stop-color="#0d3f9c"/>
      </linearGradient>
      <linearGradient id="swoosh-blue" x1="0" y1="0" x2="1" y2="0">
        <stop offset="0" stop-color="#0f3f9a"/>
        <stop offset=".55" stop-color="#0a7fd6"/>
        <stop offset="1" stop-color="#00b8f2"/>
      </linearGradient>
      <linearGradient id="swoosh-green" x1="0" y1="0" x2="1" y2="0">
        <stop offset="0" stop-color="#3e9f12"/>
        <stop offset="1" stop-color="#5cc21f"/>
      </linearGradient>
      <radialGradient id="pet-glow" cx=".45" cy=".5" r=".5">
        <stop offset="0" stop-color="#dfe4ef" stop-opacity=".85"/>
        <stop offset=".6" stop-color="#e6eaf3" stop-opacity=".55"/>
        <stop offset="1" stop-color="#eef1f7" stop-opacity="0"/>
      </radialGradient>
    </defs>
    <rect class="header-band" x="0" y="0" width="42" height="150" fill="url(#band-blue)"/>
    <rect class="header-rule" x="46" y="0" width="2" height="150" fill="var(--brand-green)"/>
    <rect class="header-edge" x="811" y="0" width="4" height="125" fill="var(--brand-blue)"/>
    <rect class="contact-divider" x="520" y="10" width="1" height="100" fill="var(--rule-grey)"/>
    <ellipse class="pet-watermark" role="img" aria-label="Faint silhouette of a dog and cat"
      cx="160" cy="770" rx="210" ry="250" fill="url(#pet-glow)"/>
    <path class="swoosh-blue" fill="url(#swoosh-blue)"
      d="M0,1055 L0,1052 Q520,1042 815,822 L815,1055 Z"/>
    <path class="swoosh-green" fill="url(#swoosh-green)"
      d="M0,1043 Q500,1018 815,762 L815,802 Q520,1030 0,1047 Z"/>
  </svg>

  <header class="brand">
    <span class="brand__dot"></span>
    <span class="brand__name">Kindpaw Vet Visits</span>
  </header>

  <ul class="contact">
    <li class="contact__item">
      <svg class="contact__icon" viewBox="0 0 20 20"><circle cx="10" cy="10" r="9" fill="none" stroke="var(--icon-blue)" stroke-width="1.4"/><path d="M7 5c-1 1-1 3 0 5s3 4 5 5c1 0 2 0 2-1l-2-2-1 1c-1-1-2-2-3-4l1-1-2-3z" fill="var(--icon-blue)"/></svg>
      <span>0400 123 987</span>
    </li>
    <li class="contact__item">
      <svg class="contact__icon" viewBox="0 0 20 20"><rect x="1" y="4" width="18" height="12" fill="var(--icon-blue)"/><path d="M1 4l9 7 9-7" fill="none" stroke="#fff" stroke-width="1.3"/></svg>
      <span>hello@kindpawvet.com.au</span>
    </li>
    <li class="contact__item">
      <svg class="contact__icon" viewBox="0 0 20 20"><circle cx="10" cy="10" r="9" fill="var(--icon-blue)"/><g fill="none" stroke="#fff" stroke-width=".9"><ellipse cx="10" cy="10" rx="4" ry="9"/><path d="M1 10h18M2.5 6h15M2.5 14h15"/></g></svg>
      <span>www.kindpawvet.com.au</span>
    </li>
  </ul>

  <address class="address">
    <div class="address__line">
      <span>Po Box 4821</span>
      <svg class="address__icon" viewBox="0 0 20 20"><path d="M10 2l9 8h-3v8h-4v-5H8v5H4v-8H1z" fill="#fff"/></svg>
    </div>
    <div class="address__line"><span>Brookhaven Qld 4059</span></div>
  </address>
</main>
</body>
</html>
```